Business card design needed

I run a Beautician studio (for 7 years now)
I offer
- Velmo Body Sugaring
- Ruby Glaze
- Nails
- Facials
- Manicure
- Foot Treatment
It might not be necessary to list all those treatments?
Maybe the link to the Website is sufficient?
I leave that up to you ...
(more info on www.FernAndDewByLenka.com.au)
Velmo BodySugaring is our biggest success, It replaces waxing.
I would like to incorporate the logo into the Business Card.
We had many complaints regarding our old Business Cards as the Phone Number was to small.
On the backside, we would like a "your next Appointment" section.
Looking forward to you Design, cheers ... Lenka
Industry/Entity Type
Business
Contact Information for Business Card
Fern by Dew by Lenka
14 Korrin Sqr 3942 Berwick
www.FernAndDewByLenka.com.au
03 9481 2267

```html
<!DOCTYPE html>
<html lang="en">
<head>
<meta charset="utf-8">
<title>Fern &amp; Dew by Lenka – Business Cards</title>
<link href="https://fonts.googleapis.com/css2?family=Cantarell&family=PT+Sans:ital,wght@0,400;0,700;1,700&family=Tinos&display=swap" rel="stylesheet">
<style>
  :root {
    --backdrop: #8a5a36;
    --card: #ffffff;
    --ink: #333333;
    --ink-soft: #555555;
    --rule: #8c8c8c;
    --marker: #c9c9c9;
  }
  * { box-sizing: border-box; margin: 0; padding: 0; }
  html, body { width: 1200px; height: 788px; overflow: hidden; }
  body {
    background: var(--backdrop);
    font-family: "PT Sans", Arial, sans-serif;
    color: var(--ink);
    position: relative;
  }
  .card {
    position: absolute;
    width: 524px;
    height: 299px;
    background: var(--card);
    border-radius: 18px;
    overflow: hidden;
  }
  .card--front { left: 338px; top: 75px; }
  .card--back-services { left: 54px; top: 446px; }
  .card--back-appointment { left: 622px; top: 446px; }
  .abs { position: absolute; }

  .studio-name {
    font-family: "Cantarell", Arial, sans-serif;
    font-weight: 400;
    font-size: 24px;
    letter-spacing: 0.5px;
    color: var(--ink);
    white-space: nowrap;
  }
  .studio-name--back { font-size: 21px; }

  /* partner name block: plain text with one square marker */
  .partner {
    display: flex;
    align-items: center;
    gap: 8px;
    font-family: "PT Sans", Arial, sans-serif;
    font-weight: 400;
    font-size: 15px;
    line-height: 18px;
    color: var(--ink);
  }
  .partner__mark { flex: none; width: 14px; height: 14px; background: var(--marker); }

  /* front */
  .contact { font-size: 17px; line-height: 23px; color: var(--ink); }
  .contact-row { display: flex; align-items: center; gap: 3px; white-space: nowrap; }
  .contact-row svg { flex: none; }

  /* back 1 */
  .title-rule { left: 0; right: 0; top: 50px; height: 1px; background: var(--rule); }
  .heading-italic { font-weight: 700; font-style: italic; font-size: 18px; }
  .service-list { list-style: none; font-family: "Tinos", "Times New Roman", serif; font-size: 15px; line-height: 20px; color: var(--ink-soft); }
  .service-list li::before { content: "■"; font-size: 7px; margin-right: 6px; vertical-align: 3px; }
  .column-divider { left: 207px; top: 82px; width: 2px; height: 132px; background: #9a9a9a; }
  .field { display: flex; align-items: flex-end; font-size: 17px; white-space: nowrap; }
  .blank { display: inline-block; border-bottom: 1px solid var(--ink); height: 18px; }
  .hours-small { font-size: 13px; white-space: nowrap; }

  /* back 2 */
  .hours-title { font-weight: 700; font-style: italic; font-size: 21px; letter-spacing: 1px; }
  .hours-lines { font-size: 18px; line-height: 24px; }
  .section-rule { left: 28px; width: 466px; top: 116px; height: 1px; background: #b5b5b5; }
  .day-row { display: flex; align-items: center; font-size: 17px; }
  .day-box { width: 22px; height: 22px; border: 1.5px solid var(--ink); margin-right: 10px; }
  .day-row span.day { margin-right: 26px; }
</style>
</head>
<body>

  <!-- Front -->
  <section class="card card--front" aria-label="Card front">
    <h1 class="abs studio-name" style="left:28px; top:92px;">FERN&amp;DEW BY LENKA</h1>
    <div class="abs partner" style="left:386px; top:88px; width:120px;">
      <span class="partner__mark"></span>
      <span>Velmo Body Sugaring</span>
    </div>
    <address class="abs contact" style="left:30px; top:239px; font-style:normal;">
      14 Korrin Sqr,<br>3942 Berwick
    </address>
    <div class="abs contact" style="left:212px; top:239px;">
      <div class="contact-row">
        <svg width="15" height="15" viewBox="0 0 16 16" aria-hidden="true"><path d="M4 1.5c.8 0 2 2.6 2 3.2 0 .8-1.3 1.2-1.3 2 0 1.3 2.6 4.1 4 4.1.8 0 1.2-1.3 2-1.3.6 0 3.2 1.2 3.2 2 0 1.2-1.6 3-3 3C6 14.5 1.5 10 1.5 4.5c0-1.4 1.3-3 2.5-3z" fill="none" stroke="#333" stroke-width="1.2"/></svg>
        <span>03 9481 2267</span>
      </div>
      <div class="contact-row">
        <svg width="15" height="15" viewBox="0 0 16 16" aria-hidden="true"><circle cx="8" cy="8" r="5" fill="#333"/></svg>
        <span>www.FernAndDewByLenka.com.au</span>
      </div>
    </div>
  </section>

  <!-- Back 1 -->
  <section class="card card--back-services" aria-label="Card back with services">
    <h2 class="abs studio-name studio-name--back" style="left:0; right:0; top:13px; text-align:center;">FERN&amp;DEW BY LENKA</h2>
    <div class="abs title-rule"></div>

    <h3 class="abs heading-italic" style="left:29px; top:68px;">I offer</h3>
    <ul class="abs service-list" style="left:29px; top:96px;">
      <li>Velmo Body Sugaring</li>
      <li>Ruby Glaze</li>
      <li>Nails</li>
      <li>Facials</li>
      <li>Manicure</li>
      <li>Foot Treatment</li>
    </ul>
    <div class="abs column-divider"></div>

    <h3 class="abs heading-italic" style="left:243px; top:68px;">An Appointment</h3>
    <div class="abs field" style="left:243px; top:110px;">Name<span class="blank" style="width:220px;"></span></div>
    <div class="abs field" style="left:243px; top:150px;">Date<span class="blank" style="width:225px;"></span></div>
    <div class="abs field" style="left:243px; top:190px;">time<span class="blank" style="width:160px;"></span>&nbsp;am / pm</div>

    <h4 class="abs heading-italic" style="left:0; right:0; top:237px; text-align:center; font-size:15px;">Hours of Operation</h4>
    <p class="abs hours-small" style="left:60px; top:260px;">Mon. to Fri.&nbsp; 7.30am - 7.00pm</p>
    <p class="abs hours-small" style="left:284px; top:260px;">Sat. 7.30am - 12.00pm</p>
  </section>

  <!-- Back 2 -->
  <section class="card card--back-appointment" aria-label="Card back with appointment">
    <h2 class="abs hours-title" style="left:36px; top:26px;">Hours of Operation</h2>
    <p class="abs hours-lines" style="left:29px; top:59px;">Monday to Friday -&nbsp; 7.30am - 7.00pm<br>Saturday - 7.30am - 12.00pm</p>
    <div class="abs partner" style="left:384px; top:62px; width:116px;">
      <span class="partner__mark"></span>
      <span>Velmo Body Sugaring</span>
    </div>
    <div class="abs section-rule"></div>

    <div class="abs field" style="left:45px; top:144px; font-size:18px;"><span class="blank" style="width:260px;"></span>&nbsp;has an appointment</div>
    <div class="abs field" style="left:34px; top:194px; font-size:18px;">
      Date :<span class="blank" style="width:40px;"></span>&nbsp; / &nbsp;<span class="blank" style="width:42px;"></span>&nbsp; / &nbsp;<span class="blank" style="width:52px;"></span>&nbsp; @ &nbsp;<span class="blank" style="width:42px;"></span>&nbsp; : &nbsp;<span class="blank" style="width:52px;"></span>am / pm
    </div>
    <div class="abs day-row" style="left:58px; top:248px;">
      <span class="day-box"></span><span class="day">Mon.</span>
      <span class="day-box"></span><span class="day">Tue.</span>
      <span class="day-box"></span><span class="day">Wed.</span>
      <span class="day-box"></span><span class="day">Thu.</span>
      <span class="day-box"></span><span class="day">Fri.</span>
    </div>
  </section>

</body>
</html>
```